Birchline Septic Solutions

Would like to see some single sided ones but would also like to see some double sided with one sided only being the logo. Owners name is Colin Vandro. Phone number is 555-214-0387
Services are pumping, inspections, installs, and repairs

Contact Information for Business Card

555-241-0387 Colin Vandro Cedarbrook, OH

```html
<!DOCTYPE html>
<html lang="en">
<head>
<meta charset="utf-8">
<title>Birchline Septic Solutions – Business Cards</title>
<link rel="stylesheet" href="https://fonts.googleapis.com/css2?family=Open+Sans:wght@400;600;700;800&display=swap">
<style>
  :root {
    --backdrop: #222222;
    --card-white: #ffffff;
    --card-grey: #f4f4f4;
    --ink: #111111;
    --teal: #25b9b2;
    --rule: #2a2a2a;
  }
  * { box-sizing: border-box; margin: 0; padding: 0; }
  html, body {
    width: 1200px; height: 779px; overflow: hidden;
    background: var(--backdrop);
    font-family: "Open Sans", Arial, sans-serif;
  }
  .stage {
    position: relative; width: 1200px; height: 779px;
    display: flex; align-items: center; justify-content: center; gap: 40px;
  }
  .card {
    position: relative; width: 540px; height: 309px;
    box-shadow: 0 10px 30px rgba(0,0,0,.45);
    overflow: hidden;
  }

  /* Contact side */
  .card--contact { background: var(--card-grey); }
  .brand--small {
    position: absolute; left: 44px; top: 66px; width: 200px;
    display: flex; align-items: center; gap: 10px;
  }
  .brand__name {
    font-weight: 800; color: var(--ink); line-height: 1.05;
    letter-spacing: .5px; text-transform: uppercase;
  }
  .brand--small .brand__name { font-size: 19px; }
  .brand__square { width: 14px; height: 14px; background: var(--teal); flex: none; }
  .divider {
    position: absolute; left: 270px; top: 52px; width: 1px; height: 150px;
    background: var(--rule);
  }
  .contact { position: absolute; left: 300px; top: 86px; }
  .contact__name { font-size: 27px; font-weight: 800; color: var(--ink); line-height: 1.1; }
  .contact__name .first { color: var(--teal); }
  .contact__city { font-size: 15px; font-weight: 600; color: var(--ink); margin-top: 6px; }
  .contact__phone {
    display: flex; align-items: center; gap: 6px;
    font-size: 15px; color: var(--ink); margin-top: 4px;
  }
  .services-badge {
    position: absolute; left: 178px; top: 218px; width: 104px; height: 30px;
    border-radius: 50%; background: var(--teal); border: 2px solid var(--ink);
    color: #fff; font-size: 12px; font-weight: 600;
    display: flex; align-items: center; justify-content: center; z-index: 2;
  }
  .services-band {
    position: absolute; left: 0; right: 0; bottom: 20px; height: 40px;
    background: var(--teal); color: #fff;
    display: flex; align-items: center; justify-content: center; gap: 10px;
    font-size: 15px; padding-top: 6px;
  }
  .services-band .dot {
    width: 8px; height: 8px; border-radius: 50%; background: #fff; display: inline-block;
  }

  /* Logo side */
  .card--logo {
    background: var(--card-white);
    display: flex; align-items: center; justify-content: center;
  }
  .brand--large { display: flex; align-items: center; gap: 18px; }
  .brand--large .brand__name { font-size: 42px; }
  .brand--large .brand__square { width: 28px; height: 28px; }
</style>
</head>
<body>
<main class="stage">
  <section class="card card--contact" aria-label="Business card, contact side">
    <div class="brand brand--small">
      <p class="brand__name">Birchline Septic Solutions</p>
      <span class="brand__square"></span>
    </div>
    <div class="divider"></div>
    <div class="contact">
      <p class="contact__name"><span class="first">Colin</span> Vandro</p>
      <p class="contact__city">Cedarbrook, OH</p>
      <p class="contact__phone">
        <svg width="13" height="13" viewBox="0 0 24 24" aria-hidden="true">
          <path fill="#25b9b2" d="M6.6 10.8a15.1 15.1 0 0 0 6.6 6.6l2.2-2.2a1 1 0 0 1 1-.25 11.4 11.4 0 0 0 3.6.57 1 1 0 0 1 1 1V20a1 1 0 0 1-1 1A17 17 0 0 1 3 4a1 1 0 0 1 1-1h3.5a1 1 0 0 1 1 1c0 1.25.2 2.45.57 3.57a1 1 0 0 1-.25 1z"/>
        </svg>
        555-241-0387
      </p>
    </div>
    <div class="services-badge">SERVICES</div>
    <div class="services-band">
      <span class="dot"></span>Pumping
      <span class="dot"></span>Inspections
      <span class="dot"></span>Installs
      <span class="dot"></span>And Repairs
    </div>
  </section>

  <section class="card card--logo" aria-label="Business card, logo side">
    <div class="brand brand--large">
      <p class="brand__name">Birchline<br>Septic Solutions</p>
      <span class="brand__square"></span>
    </div>
  </section>
</main>
</body>
</html>
```